SkyvornQ Business Cards and Stationary Design

Need a design for our business cards and stationary. I want to carry on the theme of the logo. I want the business cards to have a design on the back. I would like the business cards and the stationary to carry the same theme, design scheme, and branding

Target Market(s)

Airlines and Maintenance Facilities

Industry/Entity Type

Aviation

Contact Information for Business Card

Name
Position Title
Address: 4827 Trellis Hollow Road, Fort Pierce, Florida, 34951
Office Number
Mobile Number
Email
Website

Font styles to use
Serif
Sans Serif

Colors

Designer to choose colors to be used in the design.

```html
<!DOCTYPE html>
<html lang="en">
<head>
<meta charset="utf-8">
<title>SkyvornQ Business Card</title>
<link rel="stylesheet" href="https://fonts.googleapis.com/css2?family=Montserrat:wght@400;500;600;700&display=swap">
<style>
  :root {
    --navy: #0d2a5c;
    --sky: #1a9be6;
    --ink: #1f3560;
    --grey: #5a5f66;
    --paper: #ffffff;
    --backdrop: #e9ecf0;
  }
  * { margin: 0; padding: 0; box-sizing: border-box; }
  html, body { width: 1200px; height: 872px; overflow: hidden; }
  body {
    background: var(--backdrop);
    font-family: "Montserrat", Arial, sans-serif;
    position: relative;
  }
  .card {
    position: absolute;
    width: 540px;
    height: 309px;
    background: var(--paper);
    box-shadow: 0 10px 30px rgba(20, 30, 50, 0.18);
    overflow: hidden;
  }
  /* Back of card */
  .card--back { left: 50px; top: 281px; }
  .card--back .brand-mark {
    position: absolute; left: 50px; top: 74px;
    width: 160px; height: 160px;
    border: 12px solid var(--sky);
    border-radius: 50%;
  }
  .card--back .brand-name {
    position: absolute; left: 236px; top: 120px;
    font-weight: 700; font-size: 40px; letter-spacing: 5px;
    color: var(--navy); text-transform: uppercase;
  }
  .card--back .brand-url {
    position: absolute; left: 262px; top: 174px;
    font-size: 13px; letter-spacing: 3px; color: var(--ink);
  }
  /* Front of card */
  .card--front { left: 610px; top: 281px; }
  .card--front .brand-mark {
    position: absolute; right: 72px; top: 24px;
    width: 64px; height: 64px;
    border: 6px solid var(--sky);
    border-radius: 50%;
  }
  .card--front .brand-name {
    position: absolute; right: 30px; top: 98px;
    font-weight: 700; font-size: 30px; letter-spacing: 4px;
    color: var(--navy); text-transform: uppercase;
  }
  .accent-rule {
    position: absolute; left: 170px; right: 24px; top: 168px;
    height: 2px; background: var(--sky);
  }
  .person { position: absolute; left: 34px; top: 146px; }
  .person__name {
    font-weight: 700; font-size: 20px; color: var(--navy);
    text-transform: uppercase; letter-spacing: 0.3px;
  }
  .person__title {
    font-size: 17px; color: var(--grey); text-transform: uppercase;
    margin-top: 2px;
  }
  .contacts {
    position: absolute; left: 34px; top: 214px;
    list-style: none; font-size: 13px; color: var(--ink);
  }
  .contacts li { display: flex; align-items: center; gap: 7px; height: 18px; }
  .contacts svg { width: 13px; height: 13px; flex: none; }
  .divider {
    position: absolute; left: 222px; top: 218px;
    width: 1px; height: 50px; background: #c9cdd3;
  }
  .address {
    position: absolute; left: 236px; top: 214px;
    display: flex; gap: 7px; font-size: 13px; color: var(--ink); line-height: 18px;
  }
  .address svg { width: 13px; height: 13px; margin-top: 2px; flex: none; }
  .base-band {
    position: absolute; left: 0; right: 0; bottom: 0;
    height: 16px; background: var(--navy);
  }
</style>
</head>
<body>

<section class="card card--back" aria-label="Business card back">
  <div class="brand-mark"></div>
  <div class="brand-name">SkyvornQ</div>
  <div class="brand-url">www.skyvornq.com</div>
</section>

<section class="card card--front" aria-label="Business card front">
  <div class="brand-mark"></div>
  <div class="brand-name">SkyvornQ</div>
  <div class="accent-rule"></div>

  <div class="person">
    <div class="person__name">Darren Kellway</div>
    <div class="person__title">President</div>
  </div>

  <ul class="contacts">
    <li>
      <svg viewBox="0 0 16 16"><circle cx="8" cy="8" r="7" fill="none" stroke="#1a9be6" stroke-width="1.5"/><path d="M5 4.5l1.5-.5 1 2-1 .8a5 5 0 0 0 2.7 2.7l.8-1 2 1-.5 1.5c-3.5 0-6.5-3-6.5-6.5z" fill="#0d2a5c"/></svg>
      012-555-0147
    </li>
    <li>
      <svg viewBox="0 0 16 16"><circle cx="8" cy="8" r="7" fill="none" stroke="#1a9be6" stroke-width="1.5"/><rect x="5.5" y="3.8" width="5" height="8.4" rx="1" fill="none" stroke="#0d2a5c" stroke-width="1.3"/></svg>
      012-555-0183
    </li>
    <li>
      <svg viewBox="0 0 16 16"><circle cx="8" cy="8" r="7" fill="none" stroke="#1a9be6" stroke-width="1.5"/><rect x="4" y="5.5" width="8" height="5.5" fill="none" stroke="#0d2a5c" stroke-width="1.2"/><path d="M4 5.5l4 3 4-3" fill="none" stroke="#0d2a5c" stroke-width="1.2"/></svg>
      info@skyvornq.com
    </li>
    <li>
      <svg viewBox="0 0 16 16"><circle cx="8" cy="8" r="7" fill="none" stroke="#1a9be6" stroke-width="1.5"/><circle cx="8" cy="8" r="4" fill="none" stroke="#0d2a5c" stroke-width="1.1"/><path d="M4 8h8M8 4c-1.6 2.4-1.6 5.6 0 8M8 4c1.6 2.4 1.6 5.6 0 8" fill="none" stroke="#0d2a5c" stroke-width="1"/></svg>
      www.skyvornq.com
    </li>
  </ul>

  <div class="divider"></div>

  <div class="address">
    <svg viewBox="0 0 16 16"><circle cx="8" cy="8" r="7" fill="none" stroke="#1a9be6" stroke-width="1.5"/><path d="M8 12.5s-3-3.2-3-5.3a3 3 0 0 1 6 0c0 2.1-3 5.3-3 5.3z" fill="#0d2a5c"/><circle cx="8" cy="7.2" r="1" fill="#fff"/></svg>
    <span>4827 Trellis Hollow Road,<br>Fort Pierce, Florida, 34951</span>
  </div>

  <div class="base-band"></div>
</section>

</body>
</html>
```